Communication and Marketing agency needs a new presentation card

We are a group of communication and marketing agencies specialized in companies that are in the logistics and industrial sector. The head agency is TELVANO Grupo and the group consists of 4 agencies: TELVANO Media, TELVANO Digital, TELVANO Research and DifundeEnPantalla. We hace 4 offices in Spain (Madrid, Barcelona, Valencia and Murcia). We are looking for a clean and attractive design that transmits our experience, brand presence in the market and knowledge to those who receive the card.It has to maintain the colors of the logo that is attached.
Target Market(s)
logistics and industrial sector
Marketing department
Contact Information for Business Card
Clean and attractive design

```html
<!DOCTYPE html>
<html lang="es">
<head>
<meta charset="utf-8">
<title>TELVANO Grupo – Tarjeta de presentación</title>
<link rel="stylesheet" href="https://fonts.googleapis.com/css2?family=Open+Sans:wght@400;600;700&display=swap">
<style>
  :root {
    --backdrop: #3b322e;
    --paper: #f7f7f5;
    --charcoal: #4a4846;
    --brand-red: #b01c2a;
    --ink: #3a3a3a;
    --muted-light: #d9d7d5;
    --rule: #bdbdbd;
    --white: #ffffff;
  }
  * { box-sizing: border-box; margin: 0; padding: 0; }
  html, body {
    width: 1200px; height: 844px; overflow: hidden;
    background: var(--backdrop);
    font-family: "Open Sans", Arial, sans-serif;
  }
  .canvas {
    position: relative; width: 1200px; height: 844px;
    display: flex; align-items: center; justify-content: center; gap: 60px;
  }
  .card {
    position: relative; width: 500px; height: 290px;
    box-shadow: 0 14px 30px rgba(0,0,0,0.45);
    overflow: hidden;
  }

  /* Front */
  .card--front { background: var(--paper); color: var(--ink); }
  .front__brand {
    position: absolute; top: 40px; right: 34px;
    font-size: 30px; font-weight: 600; color: var(--brand-red);
    letter-spacing: 1px;
  }
  .front__rule {
    position: absolute; left: 34px; right: 34px; height: 1px;
    background: var(--rule);
  }
  .front__rule--top { top: 110px; }
  .front__rule--bottom { top: 222px; }
  .person { position: absolute; left: 34px; top: 130px; }
  .person__name {
    font-size: 17px; font-weight: 700; color: var(--brand-red);
    letter-spacing: 0.5px; line-height: 1.2;
  }
  .person__role { font-size: 13px; line-height: 1.3; }
  .person__address { font-size: 13px; margin-top: 12px; }
  .contacts {
    position: absolute; left: 34px; top: 232px;
    font-size: 12.5px; line-height: 1.6;
  }
  .contacts__label { color: var(--brand-red); }
  .contacts__item { margin-right: 8px; }
  .contacts__web { color: var(--brand-red); margin-left: 6px; }

  /* Back */
  .card--back { background: var(--charcoal); }
  .back__brand {
    position: absolute; top: 62px; left: 0; right: 0; text-align: center;
    font-size: 32px; font-weight: 600; color: var(--brand-red); letter-spacing: 1px;
  }
  .back__offices {
    position: absolute; top: 122px; left: 0; right: 0; text-align: center;
    font-size: 13px; color: var(--muted-light); letter-spacing: 0.5px;
  }
  .agency-band {
    position: absolute; left: 0; right: 0; bottom: 0; height: 100px;
    background: var(--brand-red);
    display: flex; align-items: center; justify-content: space-around;
    padding: 0 12px;
  }
  .agency-band__name {
    color: var(--white); font-size: 12.5px; font-weight: 600;
    text-align: center; line-height: 1.25;
  }
</style>
</head>
<body>
<main class="canvas">
  <section class="card card--front" aria-label="Frente de la tarjeta">
    <div class="front__brand">TELVANO Grupo</div>
    <div class="front__rule front__rule--top"></div>
    <div class="person">
      <p class="person__name">DANIEL HARTLEY</p>
      <p class="person__role">Managing Director</p>
      <p class="person__address">12345, Address Goes Here Country Name, 123456.</p>
    </div>
    <div class="front__rule front__rule--bottom"></div>
    <div class="contacts">
      <p>
        <span class="contacts__item"><span class="contacts__label">T:</span>(044) 123 456 789</span>
        <span class="contacts__item"><span class="contacts__label">F:</span>(044) 123456789</span>
        <span class="contacts__item"><span class="contacts__label">M:</span>(044)123456789</span>
      </p>
      <p>
        <span class="contacts__label">E:</span>info@youremail.com
        <span class="contacts__web">www.yourweb.com</span>
      </p>
    </div>
  </section>

  <section class="card card--back" aria-label="Reverso de la tarjeta">
    <div class="back__brand">TELVANO Grupo</div>
    <p class="back__offices">Sevilla, Bilbao, Zaragoza, Málaga</p>
    <div class="agency-band">
      <span class="agency-band__name">TELVANO<br>Research</span>
      <span class="agency-band__name">TELVANO<br>Digital</span>
      <span class="agency-band__name">TELVANO<br>Media</span>
      <span class="agency-band__name">DifundeEnPantalla</span>
    </div>
  </section>
</main>
</body>
</html>
```